Business card

creative business card for newly created national firm that specializes in high-density storage for retail markets. Looking for creativity and overall theme that will differentiate from others in this unique niche ...essentially a design that will provide instant recognition as we develop our identity in the marketplace. possible initial thoughts are attached with logo separately

Retail

```html
<!DOCTYPE html>
<html lang="en">
<head>
<meta charset="utf-8">
<title>Stackwell Retail Systems — Business Card</title>
<link rel="stylesheet" href="https://fonts.googleapis.com/css2?family=Cabin:ital,wght@0,500;0,700;1,500&family=Tinos:ital@1&display=swap">
<style>
  :root {
    --panel-blue: #b6e0f7;
    --card-white: #ffffff;
    --ink-teal: #1c5168;
    --mark-teal: #2e86a8;
    --tagline-teal: #3f86a6;
    --ink-black: #111111;
  }
  html, body {
    margin: 0;
    padding: 0;
    width: 1200px;
    height: 720px;
    overflow: hidden;
    background: var(--card-white);
  }
  .card {
    position: relative;
    width: 1200px;
    height: 720px;
    overflow: hidden;
    background: var(--card-white);
  }
  .brand-panel {
    position: absolute;
    left: 0;
    top: 0;
    width: 560px;
    height: 720px;
    background: var(--panel-blue);
  }
  .brand-square {
    position: absolute;
    left: 268px;
    top: 92px;
    width: 230px;
    height: 230px;
    background: var(--mark-teal);
  }
  .brand-name {
    position: absolute;
    left: 66px;
    top: 400px;
    margin: 0;
    font-family: "Cabin", sans-serif;
    font-weight: 500;
    font-size: 76px;
    line-height: 80px;
    letter-spacing: 1px;
    color: var(--ink-teal);
    text-transform: uppercase;
  }
  .brand-name span { display: block; }
  .contact {
    position: absolute;
    right: 85px;
    top: 208px;
    text-align: right;
    font-family: "Cabin", sans-serif;
  }
  .contact-name {
    margin: 0;
    font-weight: 700;
    font-size: 50px;
    line-height: 56px;
    letter-spacing: 1.5px;
    color: var(--ink-teal);
  }
  .contact-phone {
    margin: 0;
    font-weight: 500;
    font-size: 33px;
    line-height: 44px;
    color: var(--ink-black);
  }
  .tagline {
    position: absolute;
    left: 514px;
    top: 508px;
    margin: 0;
    font-family: "Tinos", serif;
    font-style: italic;
    font-size: 48px;
    line-height: 56px;
    color: var(--tagline-teal);
  }
  .tagline-square {
    position: absolute;
    left: 944px;
    top: 480px;
    width: 44px;
    height: 44px;
    background: var(--mark-teal);
  }
  .website {
    position: absolute;
    right: 85px;
    top: 608px;
    margin: 0;
    font-family: "Cabin", sans-serif;
    font-style: italic;
    font-weight: 500;
    font-size: 24px;
    line-height: 30px;
    color: var(--ink-black);
  }
</style>
</head>
<body>
  <div class="card">
    <div class="brand-panel"></div>
    <div class="brand-square"></div>
    <h1 class="brand-name"><span>Stackwell</span><span>Retail</span><span>Systems</span></h1>

    <div class="contact">
      <p class="contact-name">DANA MORRELL</p>
      <p class="contact-phone">855-SHELF-PRO</p>
    </div>

    <p class="tagline">Innovate your space</p>
    <div class="tagline-square"></div>

    <p class="website">www.stackwellretail.com</p>
  </div>
</body>
</html>
```